New Bicycle shop business card

Hi!
I'm looking for a business card for my new proffesional bike mechanics shop. This shop is only for fixing broken bikes and not selling bikes.
Peferbly a modern and sleek and modern design.
Colors: black, grey, red, white
Information:
Name: Rijwielwerkplaats Vanhoutte
Shop owner: Bart Vanhoutte & Marieke Segers
Website: www.rijwielwerkplaats-vanhoutte.be
Email: info@rijwielwerkplaats-vanhoutte.be
Phone number: +32471902368
Street adres: Kerkweg 46
9940 Bellebeke
Slogan/shop information: Herstellingen van alle merken.
Logo: see files.
Target Market(s)
People who seek a mechanic to fix or upgrade their bikes.
Contact Information for Business Card
Information:
Website: info@rijwielwerkplaats-vanhoutte.be
9940 Bellebeke
Logo: see files.

```html
<!DOCTYPE html>
<html lang="nl">
<head>
<meta charset="utf-8">
<title>Rijwielwerkplaats Vanhoutte – visitekaart</title>
<link href="https://fonts.googleapis.com/css2?family=Open+Sans:wght@400;600;700&display=swap" rel="stylesheet">
<style>
  :root{
    --ink:#1b1b1d;
    --card-dark:#151517;
    --red:#e31d3c;
    --grey:#9a9d9f;
    --paper:#f7f7f7;
    --bg:#d9d9db;
    --text:#1e1e1e;
  }
  *{box-sizing:border-box;margin:0;padding:0}
  html,body{width:1200px;height:1021px;overflow:hidden}
  body{
    background:var(--bg);
    font-family:"Open Sans",sans-serif;
    display:flex;flex-direction:column;align-items:center;justify-content:center;gap:60px;
  }
  .card{
    width:700px;height:400px;position:relative;overflow:hidden;
    box-shadow:0 10px 30px rgba(0,0,0,.25);
  }
  /* front */
  .card--front{background:var(--card-dark);color:#fff}
  .brand{
    display:flex;align-items:center;gap:16px;
    font-weight:700;text-transform:uppercase;letter-spacing:.06em;line-height:1.15;
  }
  .brand__dot{width:44px;height:44px;border-radius:50%;background:var(--red);flex:none}
  .card--front .brand{
    position:absolute;left:0;right:0;top:110px;justify-content:center;
    font-size:26px;color:#fff;
  }
  .band{position:absolute;left:0;top:242px;width:700px;height:60px}
  .band__slogan{
    position:absolute;left:0;right:0;top:258px;text-align:center;
    font-size:17px;letter-spacing:.04em;color:#fff;
  }
  /* back */
  .card--back{background:var(--paper);color:var(--text)}
  .card--back .brand{
    position:absolute;left:40px;top:160px;width:300px;
    font-size:22px;color:var(--ink);
  }
  .divider{position:absolute;left:356px;top:90px;width:2px;height:220px;background:var(--grey)}
  .divider::before{content:"";position:absolute;left:0;top:0;width:2px;height:44px;background:var(--red)}
  .details{position:absolute;left:382px;top:92px;right:20px;font-size:15px;line-height:1.45}
  .details__names{color:var(--red);font-weight:700;font-size:19px;line-height:1.25}
  .details__role{margin-bottom:16px}
  .details__address{margin-bottom:12px}
  .contact{display:flex;align-items:center;gap:8px}
  .contact svg{width:14px;height:14px;flex:none}
</style>
</head>
<body>

<section class="card card--front">
  <div class="brand"><span class="brand__dot"></span><span>Rijwielwerkplaats<br>Vanhoutte</span></div>
  <svg class="band" viewBox="0 0 700 60" aria-hidden="true">
    <polygon points="0,0 48,0 40,22 0,22" fill="var(--grey)"/>
    <polygon points="58,8 700,8 700,46 40,46" fill="var(--red)" transform="translate(0,0)"/>
    <polygon points="618,46 700,46 700,60 610,60" fill="var(--grey)"/>
  </svg>
  <p class="band__slogan">Herstellingen van alle merken.</p>
</section>

<section class="card card--back">
  <div class="brand"><span class="brand__dot"></span><span>Rijwielwerkplaats<br>Vanhoutte</span></div>
  <div class="divider"></div>
  <div class="details">
    <p class="details__names">Bart Vanhoutte &amp; Marieke Segers</p>
    <p class="details__role">Shop Owner</p>
    <p class="details__address">Kerkweg 46<br>9940 Bellebeke</p>
    <p class="contact">
      <svg viewBox="0 0 24 24" aria-hidden="true"><path fill="var(--red)" d="M6.6 10.8a15 15 0 0 0 6.6 6.6l2.2-2.2c.3-.3.7-.4 1-.2 1.1.4 2.3.6 3.6.6.6 0 1 .4 1 1V20c0 .6-.4 1-1 1A17 17 0 0 1 3 4c0-.6.4-1 1-1h3.5c.6 0 1 .4 1 1 0 1.3.2 2.5.6 3.6.1.3 0 .7-.2 1z"/></svg>
      +32471902368
    </p>
    <p class="contact">
      <svg viewBox="0 0 24 24" aria-hidden="true"><rect x="2" y="5" width="20" height="14" fill="none" stroke="var(--red)" stroke-width="2"/><path d="M2 5l10 8 10-8" fill="none" stroke="var(--red)" stroke-width="2"/></svg>
      info@rijwielwerkplaats-vanhoutte.be
    </p>
    <p class="contact">
      <svg viewBox="0 0 24 24" aria-hidden="true"><circle cx="12" cy="12" r="10" fill="none" stroke="var(--red)" stroke-width="2"/><path d="M2 12h20M12 2c3 3 3 17 0 20M12 2c-3 3-3 17 0 20" fill="none" stroke="var(--red)" stroke-width="1.6"/></svg>
      www.rijwielwerkplaats-vanhoutte.be
    </p>
  </div>
</section>

</body>
</html>
```